Website Design - TallyPorchHelpers.net

PLEASE CHECK WORD DOCUMENT ATTACHED FOR WEBSITE FLOW.

Target Market(s)

REAL ESTATE AGENTS ARE THE TARGET MARKET

Industry/Entity Type

Real Estate

Coding

Coded - Design and coding required

Number of Pages Required

4 page

Colors

Designer to choose colors to be used in the design.

Requirements
Must have
• WE LIKE RED LOGO ATTACHED
Nice to have
• PLEASE CHECK WORD DOCUMENT ATTACHED FOR WEBSITE FLOW.
Should not have

```html
<!DOCTYPE html>
<html lang="en">
<head>
<meta charset="utf-8">
<title>TallyPorchHelpers.net</title>
<link href="https://fonts.googleapis.com/css2?family=Poppins:wght@400;500;600;700&family=Barlow:wght@400;500;600;700&display=swap" rel="stylesheet">
<style>
:root{
  --red:#e5141b;
  --red-deep:#c70d14;
  --ink:#1d1d1d;
  --text:#555;
  --muted:#8a8a8a;
  --light:#f1f1f1;
  --white:#fff;
  --dark:#1c1c1c;
  --darker:#141414;
  --head:'Poppins',sans-serif;
  --body:'Barlow',sans-serif;
}
*{margin:0;padding:0;box-sizing:border-box}
html,body{width:1200px;height:3191px;overflow:hidden}
body{font-family:var(--body);color:var(--text);background:var(--white);position:relative}
.section{position:absolute;left:0;width:1200px}
.abs{position:absolute}
h2.section-title{font-family:var(--head);font-weight:600;font-size:22px;color:var(--ink);text-align:center;position:absolute;left:0;width:1200px}

/* header */
.site-header{top:0;height:81px;background:var(--white)}
.brand{left:234px;top:24px;display:flex;align-items:center;gap:8px;font-family:var(--head);font-weight:700;font-size:13px;line-height:15px;color:var(--red);z-index:2}
.brand-square{width:16px;height:16px;background:var(--red);flex:none}
.main-nav{left:0;width:1200px;top:33px;font-family:var(--head);font-size:10.5px;font-weight:500;color:#333;letter-spacing:.3px}
.main-nav span{position:absolute;white-space:nowrap}
.header-call{left:843px;top:24px;display:flex;gap:8px;align-items:center}
.header-call small{display:block;font-size:10px;color:#666}
.header-call strong{display:block;font-family:var(--head);font-size:14px;color:var(--red);font-weight:700}

/* hero */
.hero{top:81px;height:519px;background:linear-gradient(90deg,#b5402b 0%,#8d3a2a 30%,#5f3a30 60%,#3a2a24 100%)}
.hero-photo{position:absolute;inset:0;background:radial-gradient(ellipse at 65% 40%,rgba(210,170,140,.35),transparent 55%),linear-gradient(180deg,rgba(0,0,0,.05),rgba(0,0,0,.35))}
.hero-copy{position:absolute;top:214px;left:0;width:1200px;text-align:center;color:var(--white)}
.hero-copy h1{font-family:var(--head);font-weight:700;font-size:30px;letter-spacing:-.2px}
.hero-copy p{font-family:var(--head);font-weight:500;font-size:16px;line-height:24px;margin-top:6px}

/* audience */
.audience{top:600px;height:180px;background:linear-gradient(90deg,var(--red-deep),var(--red) 50%,var(--red-deep))}
.audience-base{top:780px;height:356px;background:var(--light)}
.audience h2{top:42px;color:var(--white)}
.option-card{top:704px;width:232px;height:144px;background:var(--white);border-radius:4px;box-shadow:0 6px 0 -2px var(--red),0 8px 18px rgba(0,0,0,.12);text-align:center;padding-top:24px}
.option-card svg{display:block;margin:0 auto 10px}
.option-card p{font-family:var(--head);font-size:12px;font-weight:500;color:var(--ink);line-height:15px}
.option-card p b{font-weight:600}

/* steps */
.steps-title{top:906px}
.step{top:968px;width:220px;text-align:center}
.step-num{width:44px;height:44px;border-radius:50%;background:var(--red);color:var(--white);font-family:var(--head);font-weight:600;font-size:13px;line-height:44px;margin:0 auto;box-shadow:0 0 0 5px rgba(229,20,27,.15)}
.step p{font-size:12.5px;line-height:17px;color:var(--muted);margin-top:22px}
.step-arrow{top:984px}

/* service area */
.service{top:1136px;height:411px;background:radial-gradient(ellipse at 50% 0%,#4a2620,#2a1412 55%,#150a09)}
.service h2{top:60px;color:var(--white)}
.area-card{top:117px;width:168px}
.area-photo{height:135px;background:linear-gradient(160deg,#8fb0cf,#7a8c5a 55%,#b4232a)}
.area-card h3{font-family:var(--head);font-weight:500;font-size:12.5px;color:var(--white);margin-top:22px}
.area-card p{font-size:11.5px;line-height:16px;color:#a9a09d;margin-top:10px}

/* packages */
.packages{top:1547px;height:606px;background:#f7f7f7}
.packages h2{top:55px}
.plan{top:117px;width:140px;height:421px;background:var(--white);border-radius:4px;box-shadow:0 4px 16px rgba(0,0,0,.12);overflow:hidden;text-align:center}
.plan-top{height:110px;background:linear-gradient(180deg,#fff 0,#fff 55%,#ededed 55%);position:relative}
.plan-top h3{font-family:var(--head);font-weight:500;font-size:13px;color:var(--ink);padding-top:14px}
.price{width:56px;height:56px;border-radius:50%;background:var(--red);color:var(--white);font-family:var(--head);font-weight:600;font-size:19px;line-height:56px;margin:10px auto 0}
.price sup{font-size:9px;vertical-align:top;line-height:30px}
.plan.featured .plan-top{background:linear-gradient(180deg,var(--red) 0,var(--red) 55%,#f3d0d1 55%)}
.plan.featured h3{color:var(--white)}
.plan.featured .price{background:var(--ink)}
.plan ul{list-style:none;text-align:left;padding:8px 14px 0 16px}
.plan li{font-size:10.5px;line-height:14px;color:#444;padding-left:12px;position:relative;margin-bottom:11px}
.plan li::before{content:"";position:absolute;left:0;top:3px;width:6px;height:3px;border-left:2px solid var(--red);border-bottom:2px solid var(--red);transform:rotate(-45deg)}
.plan-btn{display:block;width:102px;height:40px;margin:6px auto 0;background:var(--ink);color:var(--white);font-family:var(--head);font-size:9.5px;font-weight:600;line-height:40px}
.plan-btn.red{background:var(--red)}
.plan-btn.two{line-height:12px;padding-top:8px;font-size:8.5px}
.plan small{display:block;font-size:8.5px;line-height:12px;color:var(--muted);padding:10px 14px 0}

/* faq */
.faq{top:2153px;height:437px;background:var(--dark)}
.faq h2{top:60px;color:var(--white)}
.faq-item{width:358px;height:34px;background:var(--white);font-size:12px;color:#333;padding:0 30px 0 12px;line-height:34px;white-space:nowrap;overflow:hidden}
.faq-item::after{content:"+";position:absolute;right:12px;top:0;font-size:16px;color:#555}
.faq-item.open{background:var(--red);color:var(--white)}
.faq-item.open::after{content:"–";color:var(--white)}
.faq-answer{width:358px;height:84px;background:var(--white);font-size:11px;line-height:15px;color:#555;padding:12px}

/* news + testimonials */
.news{top:2590px;height:317px;background:var(--white)}
.news h2{font-family:var(--head);font-weight:600;font-size:20px;color:var(--ink);left:234px;top:30px}
.news-item{left:234px;width:350px;display:flex;gap:16px}
.news-photo{width:138px;height:88px;flex:none;background:linear-gradient(150deg,#8fb0cf,#6f8a4e 55%,#c1262d)}
.news-item h3{font-family:var(--head);font-weight:500;font-size:12px;color:var(--ink)}
.news-item .meta{font-size:9.5px;color:var(--muted);margin-top:3px}
.news-item .meta b{color:var(--red);font-weight:600}
.news-item p{font-size:10.5px;line-height:15px;color:var(--muted);margin-top:8px}
.testimonials{left:600px;top:0;width:600px;height:317px;background:linear-gradient(90deg,var(--red) 45%,#ef5a4f 80%,#f08a78)}
.testimonials h2{left:26px;top:30px;color:var(--white);font-family:var(--head);font-size:20px;font-weight:600}
.quote-mark{left:26px;top:72px;font-family:var(--head);font-size:26px;color:rgba(255,255,255,.6);line-height:1}
.testimonials p{left:56px;top:74px;width:310px;font-size:11px;line-height:17px;color:var(--white)}
.avatar{left:60px;top:238px;width:50px;height:50px;border-radius:50%;background:#f4d6cf;border:3px solid var(--white)}
.author{left:124px;top:246px;color:var(--white)}
.author b{font-family:var(--head);font-size:12px;font-weight:600;display:block}
.author span{font-size:10.5px}
.dots{left:318px;top:282px;display:flex;gap:4px}
.dots i{width:7px;height:7px;border-radius:50%;border:1px solid var(--white)}
.dots i.on{background:var(--white)}

/* footer */
.site-footer{top:2907px;height:238px;background:#1e1e1e;color:#a5a5a5}
.footer-col{top:40px;font-size:10.5px;line-height:15px}
.footer-col h4{font-family:var(--head);font-size:10.5px;font-weight:600;color:var(--white);margin-bottom:12px;letter-spacing:.2px}
.footer-col strong{color:var(--white);font-size:13px;font-family:var(--head)}
.socials{display:flex;gap:6px;margin-top:14px}
.socials i{width:22px;height:22px;border-radius:50%;border:1px solid #888}
.field{width:168px;height:26px;background:var(--white);font-size:10px;color:#999;padding:6px 6px;margin-bottom:8px;border-radius:2px}
.field.tall{height:44px}
.send-btn{width:168px;height:26px;background:var(--red);color:var(--white);font-family:var(--head);font-weight:600;font-size:9.5px;text-align:center;line-height:26px;border-radius:2px}
.bottom-bar{top:3145px;height:46px;background:var(--darker);color:#a5a5a5;font-size:10.5px}
.bottom-bar .copy{left:234px;top:16px}
.bottom-bar .links{left:798px;top:16px}
</style>
</head>
<body>

<header class="section site-header">
  <div class="abs brand"><span class="brand-square"></span><span>TallyPorch<br>Helpers</span></div>
  <nav class="abs main-nav">
    <span style="left:362px">HOW IT WORKS</span>
    <span style="left:468px">SERVICE AREA</span>
    <span style="left:572px">PRICING</span>
    <span style="left:643px">ABOUT US</span>
    <span style="left:726px">FAQ</span>
    <span style="left:776px;top:-1px">
      <svg width="12" height="12" viewBox="0 0 12 12"><circle cx="5" cy="5" r="3.6" fill="none" stroke="#333" stroke-width="1.6"/><path d="M7.7 7.7L11 11" stroke="#333" stroke-width="1.6"/></svg>
    </span>
  </nav>
  <div class="abs header-call">
    <svg width="20" height="20" viewBox="0 0 20 20"><path d="M5 2l3 4-2 2c1 2 3 4 5 5l2-2 4 3-2 3C9 17 3 11 2 4z" fill="none" stroke="#e5141b" stroke-width="1.6"/></svg>
    <div><small>Call Or Text Us</small><strong>1-555-014-2290</strong></div>
  </div>
</header>

<section class="section hero">
  <div class="hero-photo" role="img" aria-label="Photo of a smiling couple meeting a real estate agent outside a house with an open house sign on the lawn"></div>
  <div class="hero-copy">
    <h1>Helping agents save time and money.</h1>
    <p>We place signs and boost foot traffic to your open houses<br>using proven marketing techniques.</p>
  </div>
</section>

<section class="section audience">
  <h2 class="section-title">Choose The Option Below That Best Describes You</h2>
</section>
<section class="section audience-base"></section>

<div class="abs option-card" style="left:234px">
  <svg width="30" height="30" viewBox="0 0 30 30"><circle cx="15" cy="9" r="6" fill="#e5141b"/><path d="M4 28c0-7 5-11 11-11s11 4 11 11z" fill="#e5141b"/></svg>
  <p>I'M A<br><b>FULL ON BROKERAGE</b></p>
</div>
<div class="abs option-card" style="left:485px">
  <svg width="36" height="30" viewBox="0 0 36 30"><circle cx="18" cy="8" r="5" fill="#e5141b"/><circle cx="8" cy="11" r="4" fill="#e5141b"/><circle cx="28" cy="11" r="4" fill="#e5141b"/><path d="M10 28c0-6 4-9 8-9s8 3 8 9z" fill="#e5141b"/><path d="M1 27c0-5 3-8 7-8 2 0 3 1 4 2-2 2-3 4-3 6z" fill="#e5141b"/><path d="M35 27c0-5-3-8-7-8-2 0-3 1-4 2 2 2 3 4 3 6z" fill="#e5141b"/></svg>
  <p>I'M AN<br><b>IND. BROKER WITH A TEAM</b></p>
</div>
<div class="abs option-card" style="left:735px">
  <svg width="30" height="30" viewBox="0 0 30 30"><rect x="5" y="2" width="3" height="27" fill="#e5141b"/><rect x="22" y="2" width="3" height="27" fill="#e5141b"/><rect x="3" y="2" width="24" height="3" fill="#e5141b"/><rect x="8" y="8" width="14" height="10" fill="#e5141b"/></svg>
  <p>I NEED<br><b>SIGN PLACEMENT ASAP</b></p>
</div>

<h2 class="section-title steps-title">How It Works</h2>
<div class="abs step" style="left:237px"><div class="step-num">01</div><p>Place signs strategically in best areas according to where the open house is located</p></div>
<div class="abs step" style="left:490px"><div class="step-num">02</div><p>Pick Up the signs after the open house</p></div>
<div class="abs step" style="left:741px"><div class="step-num">03</div><p>Store custom signs for you if needed</p></div>
<svg class="abs step-arrow" style="left:452px" width="46" height="12" viewBox="0 0 46 12"><path d="M0 6h44M38 1l6 5-6 5" fill="none" stroke="#777" stroke-width="1.3"/></svg>
<svg class="abs step-arrow" style="left:704px" width="46" height="12" viewBox="0 0 46 12"><path d="M0 6h44M38 1l6 5-6 5" fill="none" stroke="#777" stroke-width="1.3"/></svg>

<section class="section service">
  <h2 class="section-title">Service Area</h2>
  <div class="abs area-card" style="left:234px"><div class="area-photo" role="img" aria-label="Photo of a red open house sign on a lawn"></div><h3>Tital Goes Here</h3><p>In publishing and graphic design, lorem ipsum is a placeholder text form of a document.</p></div>
  <div class="abs area-card" style="left:421px"><div class="area-photo" role="img" aria-label="Photo of open house signs at a street corner"></div><h3>Tital Goes Here</h3><p>In publishing and graphic design, lorem ipsum is a placeholder text form of a document.</p></div>
  <div class="abs area-card" style="left:609px"><div class="area-photo" role="img" aria-label="Photo of an open house sign in front of a home"></div><h3>Tital Goes Here</h3><p>In publishing and graphic design, lorem ipsum is a placeholder text form of a document.</p></div>
  <div class="abs area-card" style="left:796px"><div class="area-photo" role="img" aria-label="Photo of an open house sign under a blue sky"></div><h3>Tital Goes Here</h3><p>In publishing and graphic design, lorem ipsum is a placeholder text form of a document.</p></div>
</section>

<section class="section packages">
  <h2 class="section-title">Choose Your Package</h2>
  <div class="abs plan" style="left:234px">
    <div class="plan-top"><h3>5 SIGNS</h3><div class="price"><sup>$</sup>49</div></div>
    <ul><li>Place signs strategically in best areas according to where the open house is located</li><li>Pick Up the signs after the open house</li><li>Store custom signs for you if needed</li></ul>
    <span class="plan-btn">SIGN UP</span>
    <small>Sign Up For A Subscription And Get These Marketing Services For Free</small>
  </div>
  <div class="abs plan" style="left:381px">
    <div class="plan-top"><h3>10 SIGNS</h3><div class="price"><sup>$</sup>59</div></div>
    <ul><li>Place signs strategically in best areas according to where the open house is located</li><li>Pick Up the signs after the open house</li><li>Store custom signs for you if needed</li></ul>
    <span class="plan-btn">SIGN UP</span>
    <small>Sign Up For A Subscription And Get These Marketing Services For Free</small>
  </div>
  <div class="abs plan featured" style="left:530px">
    <div class="plan-top"><h3>15 SIGNS</h3><div class="price"><sup>$</sup>69</div></div>
    <ul><li>Place signs strategically in best areas according to where the open house is located</li><li>Pick Up the signs after the open house</li><li>Store custom signs for you if needed</li></ul>
    <span class="plan-btn red">SIGN UP</span>
    <small>Sign Up For A Subscription And Get These Marketing Services For Free</small>
  </div>
  <div class="abs plan" style="left:677px">
    <div class="plan-top"><h3>20 SIGNS</h3><div class="price"><sup>$</sup>79</div></div>
    <ul><li>Place signs strategically in best areas according to where the open house is located</li><li>Pick Up the signs after the open house</li><li>Store custom signs for you if needed</li></ul>
    <span class="plan-btn">SIGN UP</span>
    <small>Sign Up For A Subscription And Get These Marketing Services For Free</small>
  </div>
  <div class="abs plan" style="left:824px">
    <div class="plan-top"><h3>25+ SIGNS</h3><div style="height:66px"></div></div>
    <ul><li>Place signs strategically in best areas according to where the open house is located</li><li>Pick Up the signs after the open house</li><li>Store custom signs for you if needed</li></ul>
    <span class="plan-btn two">CLICK BUY NOW TO<br>CREATE CUSTOM PKG</span>
    <small>Sign Up For A Subscription And Get These Marketing Services For Free</small>
  </div>
</section>

<section class="section faq">
  <h2 class="section-title">Frequently Asked Questions</h2>
  <div class="abs faq-item" style="left:234px;top:118px">Vestibulum sed felis a ante suscipit auctor</div>
  <div class="abs faq-item" style="left:234px;top:162px">Sed ullamcorper augue ut facilisis condimentum</div>
  <div class="abs faq-item" style="left:234px;top:205px">Curabitur et ligula sed velit feugiat pellentesque</div>
  <div class="abs faq-item" style="left:234px;top:250px">Nam vitae velit non augue ultricies laoreet</div>
  <div class="abs faq-item" style="left:609px;top:118px">Curabitur et ligula sed velit feugiat pellentesque</div>
  <div class="abs faq-item open" style="left:609px;top:162px">Lorem Ipsum used in various languages for layouts</div>
  <div class="abs faq-answer" style="left:609px;top:196px">In publishing and graphic design, lorem ipsum is a placeholder text commonly used to demonstrate the visual form of a document in graphic design, lorem ipsum is a placeholder text used to demonstrate the visual form of a document.</div>
  <div class="abs faq-item" style="left:609px;top:292px">Sed ullamcorper augue ut facilisis condimentum</div>
  <div class="abs faq-item" style="left:609px;top:337px">Nam vitae velit non augue ultricies laoreet</div>
</section>

<section class="section news">
  <h2 class="abs">Latest News</h2>
  <article class="abs news-item" style="top:80px">
    <div class="news-photo" role="img" aria-label="Photo of an open house sign in a front yard"></div>
    <div><h3>Lorem Ipsum charsets layouts</h3><div class="meta">By <b>William Doe</b> | 03 Aug 2018</div><p>Class aptent taciti sociosqu ad litora torquent per conubia nostra, per inceptos himenaeos. Mauris in erat justo.</p></div>
  </article>
  <article class="abs news-item" style="top:187px">
    <div class="news-photo" style="background:linear-gradient(150deg,#b9cbe0,#5c7da8 50%,#d9c7b2)" role="img" aria-label="Photo of an agent greeting clients at a front door"></div>
    <div><h3>Lorem Ipsum charsets layouts</h3><div class="meta">By <b>William Doe</b> | 03 Aug 2018</div><p>Class aptent taciti sociosqu ad litora torquent per conubia nostra, per inceptos himenaeos. Mauris in erat justo.</p></div>
  </article>
  <div class="abs testimonials" role="img" aria-label="Soft faded portrait of a client blended into the red background">
    <h2 class="abs">Testimonials</h2>
    <div class="abs quote-mark">“</div>
    <p class="abs">Class aptent taciti sociosqu ad litora torquent per conubia nostra, per inceptos himenaeos. Mauris in condimentum elit amet a augue. Sed non neque elit. Sed ut imperdiet nisi. Proin condimentum fermentum nunc. Etiam pharetra, erat sed fermentum feugiat, velit mauris egestas quam, ut aliquam massa nisl quis neque. Suspendisse in orci enim. Mauris in condimentum sit amet a augue. Sed non fermentum feugiat, velit mauris egestas quam, nisl quis neque.</p>
    <div class="abs avatar"></div>
    <div class="abs author"><b>– John Smith</b><span>Lorem Ipsum dolor</span></div>
    <div class="abs dots"><i class="on"></i><i></i><i></i><i></i><i></i></div>
  </div>
</section>

<footer class="section site-footer">
  <div class="abs footer-col" style="left:234px;width:190px">
    <h4>ABOUT TALLY PORCH HELPERS</h4>
    <p>Helping agents leverage their time and skills to increase production at an affordable price with impeccable support.</p>
    <div class="socials"><i></i><i></i><i></i><i></i><i></i></div>
  </div>
  <div class="abs footer-col" style="left:464px;width:180px">
    <h4>CONTACT INFORMATION</h4>
    <p>420 Lorem Ipsum dolor,<br>Suite 210, dools, TX 70000</p>
    <p style="margin-top:8px">Call Or Text Us:<br><strong>1-555-014-2290</strong></p>
    <p style="margin-top:8px">Email Us:<br>info@tallyporchhelpers.net</p>
  </div>
  <div class="abs footer-col" style="left:670px">
    <h4>QUICK LINKS</h4>
    <p style="line-height:21px">How It Works<br>Service Area<br>Pricing<br>About Us<br>FAQ</p>
  </div>
  <div class="abs footer-col" style="left:796px">
    <h4>QUICK CONTACT</h4>
    <div class="field">Your Name</div>
    <div class="field">Email Address</div>
    <div class="field tall">Message</div>
    <div class="send-btn">SEND A MESSAGE</div>
  </div>
</footer>

<div class="section bottom-bar">
  <span class="abs copy">Copyright © 2018 TallyPorchHelpers.net</span>
  <span class="abs links">Terms of Use | Privacy | Sitemap</span>
</div>

</body>
</html>
```